The book is called "Distance Racing Blueprints: An In-Depth Manual for Achieving Your Peak Race Day - Featuring Schedules, Counsel and Target-Reaching Pointers "

It is a 6" x 9" book with 205 pages. This is an advanced book for runners who have been running and trying to hit their marathon goals, but haven't been able to do so. This needs to portray a professional coaching image and high performing athlete.

I have running photos of myself running marathons if you thought that was the route to take, but I'm open to your creative influence.

```html
<!DOCTYPE html>
<html lang="en">
<head>
<meta charset="utf-8">
<title>Distance Racing Blueprints – Cover Wrap</title>
<link href="https://fonts.googleapis.com/css2?family=Montserrat:wght@700;800&family=Noto+Serif:ital@1&family=Arimo&display=swap" rel="stylesheet">
<style>
  :root {
    --stage: #2b2b2b;
    --paper: #ffffff;
    --ink: #111111;
    --red: #e41e26;
    --gold: #f9b71c;
    --photo-warm: #f6c7b8;
    --photo-cool: #c9c3e6;
  }
  html, body {
    margin: 0;
    width: 1200px;
    height: 1200px;
    overflow: hidden;
    background: var(--stage);
  }
  .wrap {
    position: absolute;
    left: 50px;
    top: 211px;
    width: 1100px;
    height: 778px;
    background: var(--paper);
    color: var(--ink);
  }
  .title-svg { position: absolute; display: block; overflow: visible; }
  .title-svg text {
    font-family: "Montserrat", sans-serif;
    font-weight: 800;
  }
  .red { fill: var(--red); }
  .gold { fill: var(--gold); }
  .black { fill: var(--ink); }

  .back-title { left: 48px; top: 40px; width: 212px; height: 100px; }
  .back-tagline {
    position: absolute;
    left: 272px;
    top: 56px;
    width: 202px;
    margin: 0;
    font-family: "Noto Serif", serif;
    font-style: italic;
    font-size: 13px;
    line-height: 19px;
    text-align: right;
  }
  .blurb {
    position: absolute;
    left: 48px;
    top: 172px;
    width: 422px;
    font-family: "Arimo", sans-serif;
    font-size: 13.2px;
    line-height: 18px;
    text-align: justify;
  }
  .blurb p { margin: 0 0 18px; }

  .spine {
    position: absolute;
    left: 529px;
    top: 0;
    width: 40px;
    height: 778px;
  }
  .spine-title, .spine-author {
    position: absolute;
    writing-mode: vertical-rl;
    font-family: "Montserrat", sans-serif;
    font-weight: 800;
    white-space: nowrap;
  }
  .spine-title { left: 8px; top: 36px; font-size: 24px; letter-spacing: 0.5px; }
  .spine-title .red { color: var(--red); }
  .spine-title .gold { color: var(--gold); }
  .spine-title .black { color: var(--ink); }
  .spine-author { left: 12px; top: 594px; font-size: 16px; letter-spacing: 1.5px; }

  .front-title { left: 625px; top: 38px; width: 438px; height: 196px; }
  .front-subtitle {
    position: absolute;
    left: 624px;
    top: 246px;
    width: 440px;
    margin: 0;
    font-family: "Noto Serif", serif;
    font-style: italic;
    font-size: 14px;
    line-height: 20px;
    text-align: center;
  }
  .hero-photo {
    position: absolute;
    left: 614px;
    top: 300px;
    width: 452px;
    height: 392px;
    background:
      radial-gradient(ellipse at 55% 45%, var(--photo-warm) 0%, rgba(246,199,184,0.5) 35%, rgba(255,255,255,0) 70%),
      radial-gradient(ellipse at 25% 55%, var(--photo-cool) 0%, rgba(255,255,255,0) 45%),
      var(--paper);
  }
  .author-name {
    position: absolute;
    left: 614px;
    top: 703px;
    width: 452px;
    margin: 0;
    text-align: center;
    font-family: "Montserrat", sans-serif;
    font-weight: 800;
    font-size: 36px;
    line-height: 1;
    letter-spacing: 1.5px;
  }
</style>
</head>
<body>
  <div class="wrap">
    <section class="back-cover">
      <svg class="title-svg back-title" viewBox="0 0 212 100" aria-label="Distance Racing Blueprints">
        <text class="red" x="0" y="28" font-size="31" textLength="212" lengthAdjust="spacingAndGlyphs">DISTANCE</text>
        <text class="gold" x="0" y="61" font-size="31" textLength="212" lengthAdjust="spacing">RACING</text>
        <text class="black" x="0" y="94" font-size="31" textLength="212" lengthAdjust="spacingAndGlyphs">BLUEPRINTS</text>
      </svg>
      <p class="back-tagline">An In-Depth Manual for Achieving Your Peak Race Day - Featuring Schedules, Counsel and Target-Reaching Pointers</p>
      <div class="blurb">
        <p>Lorem ipsum dolor sit amet, consectetur adipiscing elit, sed do eiusmod tempor incididunt ut labore et dolore magna aliqua. Quis ipsum suspendisse ultrices gravida. Risus commodo viverra maecenas accumsan lacus vel facilisis. Lorem ipsum dolor sit amet, consectetur adipiscing elit, sed do eiusmod tempor incididunt ut labore et dolore magna aliqua. Quis ipsum suspendisse ultrices gravida. Risus commodo viverra maecenas accumsan lacus vel facilisis. Lorem ipsum dolor sit amet, consectetur adipiscing elit, sed do eiusmod tempor incididunt ut labore et dolore magna aliqua. Quis ipsum suspendisse ultrices gravida. Risus commodo viverra maecenas accumsan lacus vel facilisis. Lorem ipsum dolor sit amet, consectetur adipiscing elit, sed do eiusmod tempor incididunt ut labore et dolore magna aliqua. Quis ipsum suspendisse ultrices gravida. Risus commodo viverra maecenas accumsan lacus vel facilisis.</p>
        <p>Lorem ipsum dolor sit amet, consectetur adipiscing elit, sed do eiusmod tempor incididunt ut labore et dolore magna aliqua. Quis ipsum suspendisse ultrices gravida. Risus commodo viverra maecenas accumsan lacus vel facilisis. Lorem ipsum dolor sit amet, consectetur adipiscing elit, sed do eiusmod tempor incididunt ut labore et dolore magna aliqua. Quis ipsum suspendisse ultrices gravida. Risus commodo viverra maecenas accumsan lacus vel facilisis. Lorem ipsum dolor sit amet, consectetur adipiscing elit, sed do eiusmod tempor incididunt ut labore et dolore magna aliqua. Quis ipsum suspendisse ultrices gravida. Risus commodo viverra maecenas accumsan lacus vel facilisis.</p>
      </div>
    </section>

    <section class="spine">
      <div class="spine-title"><span class="red">DISTANCE</span> <span class="gold">RACING</span> <span class="black">BLUEPRINTS</span></div>
      <div class="spine-author">AUTHOR NAME</div>
    </section>

    <section class="front-cover">
      <svg class="title-svg front-title" viewBox="0 0 438 196" aria-label="Distance Racing Blueprints">
        <text class="red" x="0" y="52" font-size="72" textLength="438" lengthAdjust="spacingAndGlyphs">DISTANCE</text>
        <text class="gold" x="0" y="122" font-size="72" textLength="438" lengthAdjust="spacing">RACING</text>
        <text class="black" x="0" y="191" font-size="72" textLength="438" lengthAdjust="spacingAndGlyphs">BLUEPRINTS</text>
      </svg>
      <p class="front-subtitle">An In-Depth Manual for Achieving Your Peak Race Day - Featuring Schedules, Counsel and Target-Reaching Pointers</p>
      <div class="hero-photo" role="img" aria-label="Photo of a group of runners in colourful athletic wear, the lead runner breaking a red finish-line tape with arms raised"></div>
      <p class="author-name">AUTHOR NAME</p>
    </section>
  </div>
</body>
</html>
```